20 year old business card needs re-design

We need to redesign our corporate business card look. We need something that appears more modern, eye catchy but professional.

Target Market(s)

manufacturing industry

Industry/Entity Type

Manufacturer

Contact Information for Business Card

One side can have the logo. Other side can have contact information.

Font styles to use
Serif

Colors
3277b5
33b8a4
ffffff

Requirements
Must have
• Eye catchy - need to standout from the crowd. company logo cannot change. Full name, job title, phone number and email address.
Should not have
• Fax, business address is not necessary.

```html
<!DOCTYPE html>
<html lang="en">
<head>
<meta charset="utf-8">
<title>Norvane Industrial — Business Card</title>
<link rel="stylesheet" href="https://fonts.googleapis.com/css2?family=Libre+Baskerville:wght@700&family=Roboto:wght@400&display=swap">
<style>
  :root {
    --brand-blue: #3277b5;
    --brand-blue-deep: #2a6aa8;
    --brand-teal: #33b8a4;
    --card-white: #ffffff;
    --ink: #2b2b2b;
    --ink-soft: #444444;
    --stage: #e9ebee;
  }
  * { margin: 0; padding: 0; box-sizing: border-box; }
  html, body { width: 1200px; height: 834px; overflow: hidden; }
  body {
    background: var(--stage);
    font-family: "Roboto", Arial, sans-serif;
    display: flex;
    align-items: center;
    justify-content: center;
    gap: 60px;
  }
  .card {
    position: relative;
    width: 520px;
    height: 297px;
    background: var(--card-white);
    box-shadow: 0 6px 20px rgba(0,0,0,0.15);
    overflow: hidden;
  }

  /* Front */
  .card--front .wordmark {
    position: absolute;
    top: 92px;
    left: 0;
    right: 0;
    text-align: center;
  }
  .wordmark-text {
    font-family: "Libre Baskerville", Georgia, serif;
    font-weight: 700;
    color: var(--ink);
    letter-spacing: -0.5px;
  }
  .card--front .wordmark-text { font-size: 40px; }
  .card--front .tagline-band {
    position: absolute;
    left: 0; right: 0;
    top: 196px;
    height: 54px;
    background: var(--brand-blue);
    display: flex;
    align-items: center;
    justify-content: center;
  }
  .tagline {
    color: var(--card-white);
    font-size: 12px;
    line-height: 1.35;
    text-align: center;
  }

  /* Back */
  .card--back .wordmark {
    position: absolute;
    top: 38px;
    right: 34px;
  }
  .card--back .wordmark-text { font-size: 27px; }
  .contact {
    position: absolute;
    left: 40px;
    top: 140px;
  }
  .contact-name {
    font-family: "Libre Baskerville", Georgia, serif;
    font-weight: 700;
    font-size: 15px;
    color: var(--ink);
  }
  .contact-title {
    font-size: 11px;
    color: var(--brand-blue);
    margin-top: 2px;
    margin-bottom: 12px;
  }
  .contact-list { list-style: none; }
  .contact-list li {
    display: flex;
    align-items: center;
    gap: 10px;
    font-size: 11.5px;
    color: var(--ink-soft);
    margin-bottom: 7px;
  }
  .contact-list svg { width: 14px; height: 14px; flex: none; }
  .footer-band {
    position: absolute;
    left: 0; right: 0; bottom: 0;
    height: 46px;
    background: var(--brand-blue-deep);
    border-top: 4px solid var(--brand-teal);
  }
</style>
</head>
<body>
  <section class="card card--front" aria-label="Card front">
    <div class="wordmark"><span class="wordmark-text">Norvane Industrial</span></div>
    <div class="tagline-band">
      <p class="tagline">International Manufacturing Solutions for OEM<br>customers in North America</p>
    </div>
  </section>

  <section class="card card--back" aria-label="Card back">
    <div class="wordmark"><span class="wordmark-text">Norvane Industrial</span></div>
    <div class="contact">
      <p class="contact-name">Daniel Reyes</p>
      <p class="contact-title">President</p>
      <ul class="contact-list">
        <li>
          <svg viewBox="0 0 24 24" fill="none" stroke="#33b8a4" stroke-width="2" stroke-linecap="round" stroke-linejoin="round"><path d="M5 3h4l2 5-3 2a12 12 0 0 0 6 6l2-3 5 2v4a2 2 0 0 1-2 2A18 18 0 0 1 3 5a2 2 0 0 1 2-2z"/></svg>
          555-014-2200 x104
        </li>
        <li>
          <svg viewBox="0 0 24 24" fill="none" stroke="#33b8a4" stroke-width="2" stroke-linejoin="round"><rect x="3" y="5" width="18" height="14"/><path d="M3 5l9 8 9-8"/></svg>
          daniel@norvaneindustrial.com
        </li>
        <li>
          <svg viewBox="0 0 24 24" fill="none" stroke="#33b8a4" stroke-width="2"><circle cx="12" cy="12" r="9"/><path d="M3 12h18M12 3c3 3 3 15 0 18M12 3c-3 3-3 15 0 18"/></svg>
          www.norvaneindustrial.com
        </li>
      </ul>
    </div>
    <div class="footer-band"></div>
  </section>
</body>
</html>
```